Larkfield Ridge Management

I need a professional website. My current website is larkfieldridgemanagement.com and I hate it. It was created with some AI tool very quickly because I needed a site up and running with no advanced notice. I’m open to all designs .. I trust you, the professionals will deliver the results I’m anxiously awaiting! :)

```html
<!DOCTYPE html>
<html lang="en">
<head>
<meta charset="utf-8">
<title>Larkfield Ridge Management</title>
<link href="https://fonts.googleapis.com/css2?family=Outfit:ital,wght@0,300;0,400;0,500;0,600;0,700;1,400&display=swap" rel="stylesheet">
<style>
:root{
  --navy:#17325e;
  --navy-deep:#0f2447;
  --red:#e8262b;
  --red-soft:#f7cfd0;
  --ink:#1f2a3d;
  --muted:#4a5366;
  --line:#e3e6ec;
  --pink:#fdecec;
  --white:#ffffff;
  --star:#f5a623;
}
*{box-sizing:border-box;margin:0;padding:0}
html,body{width:1200px;height:3974px;overflow:hidden;background:var(--white)}
body{font-family:"Outfit",sans-serif;color:var(--ink)}
.page{position:relative;width:1200px;height:3974px;overflow:hidden}
.abs{position:absolute}
a{color:inherit;text-decoration:none}

/* header */
.site-header{position:absolute;top:0;left:0;width:1200px;height:68px;background:var(--white);z-index:5}
.brand{position:absolute;left:123px;top:22px;display:flex;align-items:center;gap:8px;font-weight:700;font-size:16px;color:var(--navy)}
.brand-square{width:14px;height:14px;background:var(--red)}
.nav{position:absolute;top:27px;left:495px;font-size:11px;font-weight:400;color:var(--ink)}
.nav a{position:absolute;white-space:nowrap}
.nav a.active{color:var(--red);font-weight:600}
.btn{position:absolute;display:flex;align-items:center;justify-content:center;font-weight:600;font-size:10.5px}
.btn-red{background:var(--red);color:var(--white)}
.btn-white{background:var(--white);color:var(--navy)}
.arrow-box{position:absolute;display:flex;align-items:center;justify-content:center}
.arrow-box svg{width:12px;height:12px}

/* hero */
.hero-photo{position:absolute;top:68px;left:0;width:1200px;height:742px;
  background:linear-gradient(90deg,rgba(18,36,72,.92) 0%,rgba(25,45,85,.75) 40%,rgba(90,105,130,.35) 70%,rgba(120,130,150,.2) 100%),linear-gradient(180deg,#3c4d6e 0%,#6f7d94 50%,#3d4a60 100%);
  clip-path:polygon(0 0,100% 0,100% 592px,50% 742px,0 592px)}
.hero-title{position:absolute;left:126px;top:236px;font-size:46px;line-height:46px;font-weight:600;color:var(--white)}
.hero-title span{color:var(--red)}
.hero-text{position:absolute;left:126px;top:398px;width:440px;font-size:13px;line-height:19px;font-weight:600;color:var(--white)}

/* about */
.collage{position:absolute;background:linear-gradient(160deg,#8d8c88,#3a3835 55%,#b08563)}
.about-title{position:absolute;left:660px;top:966px;font-size:28px;line-height:31px;font-weight:600;color:var(--navy)}
.about-text{position:absolute;left:660px;width:360px;font-size:10px;line-height:15.5px;color:var(--muted)}

/* services */
.services-title{position:absolute;top:1578px;left:0;width:1200px;text-align:center;font-size:28px;font-weight:600;color:var(--white)}
.svc{position:absolute;width:260px;text-align:center;color:var(--white)}
.svc h3{font-size:16px;font-weight:600;margin-top:14px}
.svc p{font-size:10px;line-height:15.5px;margin-top:14px;padding:0 8px}
.svc svg{width:70px;height:70px}
.svc-card-frame{position:absolute;left:426px;top:1666px;width:347px;height:347px;border:1.5px solid var(--white)}
.svc-card{position:absolute;left:434px;top:1674px;width:333px;height:331px;background:var(--white)}
.svc.featured{color:var(--navy)}
.svc.featured p{color:var(--muted)}

/* approach */
.approach-title{position:absolute;top:2228px;left:0;width:1200px;text-align:center;font-size:30px;font-weight:600;color:var(--navy)}
.approach-list{position:absolute;left:183px;width:352px;list-style:none}
.approach-item{position:absolute;left:0;width:352px;border-bottom:1px solid var(--line);font-size:11.5px;font-weight:600;color:var(--navy)}
.approach-item .ic{position:absolute;right:20px;top:1px;width:10px;height:10px}
.approach-item p{font-size:9px;font-weight:400;line-height:15px;color:var(--muted);margin-top:12px;width:340px}
.approach-accent{position:absolute;background:var(--red-soft)}
.approach-photo{position:absolute;left:597px;top:2303px;width:477px;height:395px;background:linear-gradient(180deg,#a6aeb8 0%,#767f8a 45%,#2a2f3a 80%,#9aa2ad 100%);box-shadow:0 14px 40px rgba(20,30,60,.18)}

/* testimonial */
.quote{position:absolute;top:3001px;left:0;width:1200px;text-align:center;font-size:20px;line-height:25px;font-style:italic;color:var(--navy)}
.stars{position:absolute;top:3086px;left:0;width:1200px;text-align:center}
.dots{position:absolute;top:3131px;left:0;width:1200px;display:flex;justify-content:center;gap:8px}
.dots i{width:7px;height:7px;border-radius:50%;background:#cfd3da;display:block}
.dots i.on{background:var(--red)}

/* cta */
.cta{position:absolute;left:171px;top:3208px;width:856px;height:275px;background:linear-gradient(135deg,#ee2c2f,#e32126 60%,#ea4a4c)}
.cta h2{position:absolute;top:60px;width:100%;text-align:center;font-size:34px;font-weight:600;color:var(--white)}
.cta p{position:absolute;top:116px;width:100%;text-align:center;font-size:12px;line-height:19px;color:var(--white)}

/* footer */
.footer-brand{position:absolute;left:170px;top:3706px;display:flex;align-items:center;gap:10px;font-size:22px;font-weight:700;color:var(--white)}
.footer-brand .brand-square{width:22px;height:22px}
.fcol{position:absolute;top:3651px;color:var(--white)}
.fcol h4{font-size:16px;font-weight:600;margin-bottom:16px}
.fcol li{list-style:none;font-size:10.5px;line-height:22px}
.contact-row{position:relative;padding-left:18px;font-size:10.5px;line-height:15px;margin-bottom:13px}
.contact-row b{font-weight:600;display:block}
.contact-row svg{position:absolute;left:0;top:2px;width:11px;height:11px}
.footer-rule{position:absolute;left:140px;top:3922px;width:920px;height:1px;background:rgba(255,255,255,.15)}
.copyright{position:absolute;top:3940px;left:0;width:1200px;text-align:center;font-size:10px;color:rgba(255,255,255,.85)}
.to-top{position:absolute;left:1101px;top:3904px;width:37px;height:37px;background:var(--red);display:flex;align-items:center;justify-content:center}
</style>
</head>
<body>
<div class="page">

  <header class="site-header">
    <div class="brand"><span class="brand-square"></span>Larkfield Ridge Management</div>
    <nav class="nav">
      <a class="active" style="left:0">HOME</a>
      <a style="left:55px">Services</a>
      <a style="left:117px">About</a>
      <a style="left:170px">Properties</a>
      <a style="left:243px">Resources</a>
      <a style="left:314px">Contact</a>
    </nav>
    <a class="btn btn-red" style="left:873px;top:17px;width:159px;height:35px">Get a Free Consultation</a>
    <span class="arrow-box btn-red" style="left:1036px;top:17px;width:38px;height:35px"><svg viewBox="0 0 12 12"><path d="M3 9 9 3M4 3h5v5" fill="none" stroke="#fff" stroke-width="1.4"/></svg></span>
  </header>

  <section class="hero">
    <div class="hero-photo" role="img" aria-label="Photo of a white two-storey house with a dark roof among bare trees at dusk"></div>
    <svg class="abs" style="left:0;top:0" width="1200" height="830"><polygon points="46,679 600,805 1154,679 600,816" fill="#e8262b"/></svg>
    <h1 class="hero-title">Property Management<br>That <span>Protects</span><br>Your Investment.</h1>
    <p class="hero-text">Professional property management solutions designed to maximize returns, preserve property value, &amp; create exceptional experiences for owners and tenants alike.</p>
    <a class="btn btn-red" style="left:126px;top:475px;width:159px;height:36px">Get a Free Consultation</a>
    <span class="arrow-box btn-red" style="left:290px;top:475px;width:37px;height:36px"><svg viewBox="0 0 12 12"><path d="M3 9 9 3M4 3h5v5" fill="none" stroke="#fff" stroke-width="1.4"/></svg></span>
    <a class="btn btn-white" style="left:333px;top:475px;width:144px;height:36px">Explore Our Services</a>
    <span class="arrow-box btn-white" style="left:481px;top:475px;width:37px;height:36px"><svg viewBox="0 0 12 12"><path d="M3 9 9 3M4 3h5v5" fill="none" stroke="#17325e" stroke-width="1.4"/></svg></span>
  </section>

  <section class="about">
    <div class="collage" style="left:171px;top:1004px;width:137px;height:236px" role="img" aria-label="Photo of a property manager in a suit"></div>
    <div class="collage" style="left:313px;top:967px;width:137px;height:344px" role="img" aria-label="Photo of a colleague reviewing documents on a tablet"></div>
    <div class="collage" style="left:455px;top:928px;width:136px;height:383px" role="img" aria-label="Photo of a client in a tan coat"></div>
    <svg class="abs" style="left:313px;top:1064px" width="278" height="110"><path d="M0 3H278M0 105H278" stroke="#fff" stroke-width="3"/></svg>
    <h2 class="about-title">About Our Property<br>Management Solutions</h2>
    <p class="about-text" style="top:1044px">Our organization delivers comprehensive property management solutions that optimize asset performance and tenant satisfaction. By integrating advanced analytics with proven operational frameworks, our specialists ensure each property achieves sustained value appreciation.</p>
    <p class="about-text" style="top:1132px">Drawing on decades of collective expertise, the team facilitates regulatory compliance, cost efficiency, and proactive maintenance. This disciplined approach enables owners to preserve capital, enhance occupancy rates, and demonstrate long-term resilience across diverse market conditions.</p>
    <a class="btn btn-red" style="left:660px;top:1229px;width:97px;height:37px">Read More</a>
    <span class="arrow-box btn-red" style="left:762px;top:1229px;width:37px;height:37px"><svg viewBox="0 0 12 12"><path d="M3 9 9 3M4 3h5v5" fill="none" stroke="#fff" stroke-width="1.4"/></svg></span>
  </section>

  <section class="services">
    <svg class="abs" style="left:0;top:1400px" width="1200" height="780">
      <polygon points="0,160 600,19 1200,160 600,32" fill="#17325e"/>
      <polygon points="0,173 600,42 1200,173 1200,613 600,744 0,613" fill="#17325e"/>
      <polygon points="0,626 600,764 1200,626 600,751" fill="#17325e"/>
    </svg>
    <h2 class="services-title">Comprehensive Property Management Services</h2>
    <div class="svc-card-frame"></div>
    <div class="svc-card"></div>
    <div class="svc" style="left:128px;top:1720px">
      <svg viewBox="0 0 70 70" fill="none" stroke="#fff" stroke-width="2"><path d="M35 12 60 25 35 38 10 25Z"/><path d="M10 34 35 47 60 34"/><path d="M10 43 35 56 60 43"/></svg>
      <h3>Basic Service</h3>
      <p>Describe important details like price, value, length of service, and why it's unique. Or use these sections to showcase different key values of your products or services.</p>
    </div>
    <div class="svc featured" style="left:470px;top:1720px">
      <svg viewBox="0 0 70 70" fill="none" stroke="#e8262b" stroke-width="1.8"><circle cx="38" cy="22" r="7"/><circle cx="38" cy="22" r="13" stroke-dasharray="5 3"/><path d="M8 50c8-6 16-8 24-5h12c3 0 3 5 0 5H32M8 58c10-4 20-2 30 0l22-12c3-2 1-6-2-5L44 48"/></svg>
      <h3>Intermediate Service</h3>
      <p>Describe important details like price, value, length of service, and why it's unique. Or use these sections to showcase different key values of your products or services.</p>
      <svg style="width:14px;height:14px;margin-top:18px" viewBox="0 0 14 14" fill="none" stroke="#e8262b" stroke-width="1.5"><path d="M2 7h10M8 3l4 4-4 4"/></svg>
    </div>
    <div class="svc" style="left:812px;top:1720px">
      <svg viewBox="0 0 70 70" fill="none" stroke="#fff" stroke-width="2"><circle cx="35" cy="35" r="15"/><circle cx="35" cy="35" r="24" stroke-dasharray="7 4"/><path d="M26 42l6-6 4 4 9-10M40 30h5v5"/></svg>
      <h3>Advanced Service</h3>
      <p>Describe important details like price, value, length of service, and why it's unique. Or use these sections to showcase different key values of your products or services.</p>
    </div>
  </section>

  <section class="approach">
    <h2 class="approach-title">The Difference Is in Our Approach</h2>
    <ul class="approach-list">
      <li class="approach-item" style="top:2358px;height:80px">Basic Service<svg class="ic" viewBox="0 0 10 10"><path d="M2 8 8 2M3 2h5v5" fill="none" stroke="#e8262b" stroke-width="1.2"/></svg>
        <p>Our knowledgeable team brings industry experience and proven processes to effectively manage residential and investment properties.</p></li>
      <li class="approach-item" style="top:2446px;height:33px">Transparent Communication<svg class="ic" viewBox="0 0 10 10"><path d="M2 8 8 2M3 2h5v5" fill="none" stroke="#e8262b" stroke-width="1.2"/></svg></li>
      <li class="approach-item" style="top:2494px;height:33px">Fast &amp; Reliable Maintenance<svg class="ic" viewBox="0 0 10 10"><path d="M2 8 8 2M3 2h5v5" fill="none" stroke="#e8262b" stroke-width="1.2"/></svg></li>
      <li class="approach-item" style="top:2540px;height:33px">Accurate Financial Reporting<svg class="ic" viewBox="0 0 10 10"><path d="M2 8 8 2M3 2h5v5" fill="none" stroke="#e8262b" stroke-width="1.2"/></svg></li>
      <li class="approach-item" style="top:2590px;height:33px">Tenant-First Management<svg class="ic" viewBox="0 0 10 10"><path d="M2 8 8 2M3 2h5v5" fill="none" stroke="#e8262b" stroke-width="1.2"/></svg></li>
      <li class="approach-item" style="top:2635px;height:26px;border-bottom:none">Protecting Your Long-Term Investment<svg class="ic" viewBox="0 0 10 10"><path d="M2 8 8 2M3 2h5v5" fill="none" stroke="#e8262b" stroke-width="1.2"/></svg></li>
    </ul>
    <div class="approach-accent" style="left:1008px;top:2632px;width:96px;height:96px" role="img" aria-label="Decorative red dot pattern accent"></div>
    <div class="approach-photo" role="img" aria-label="Photo of three property managers in business suits standing outside a modern office building"></div>
  </section>

  <section class="testimonial">
    <svg class="abs" style="left:0;top:2770px" width="1200" height="720">
      <defs><linearGradient id="pinkfade" x1="0" y1="0" x2="0" y2="1"><stop offset="0" stop-color="#fde8e9"/><stop offset="1" stop-color="#ffffff"/></linearGradient></defs>
      <polygon points="0,155 600,22 1200,155 1200,720 0,720" fill="url(#pinkfade)"/>
      <polygon points="46,145 600,11 1154,145 600,23" fill="#e8262b"/>
    </svg>
    <svg class="abs" style="left:563px;top:2892px" width="74" height="62" viewBox="0 0 74 62"><path d="M4 58V34C4 16 13 6 30 3l2 8c-9 3-13 8-13 15h12v32Zm38 0V34c0-18 9-28 26-31l2 8c-9 3-13 8-13 15h12v32Z" fill="#17325e"/></svg>
    <p class="quote">"Larkfield Ridge Management has completely changed the<br>way we manage our rental portfolio. Professional, responsive, and<br>incredibly organized."</p>
    <div class="stars">
      <svg width="104" height="18" viewBox="0 0 104 18" fill="#f5a623">
        <g id="st"><path d="M9 1l2.4 5.2 5.6.6-4.2 3.8 1.2 5.5L9 13.3 4 16.1l1.2-5.5L1 6.8l5.6-.6Z"/></g>
        <use href="#st" x="21"/><use href="#st" x="42"/><use href="#st" x="63"/><use href="#st" x="84"/>
      </svg>
    </div>
    <div class="dots"><i class="on"></i><i></i><i></i></div>
  </section>

  <svg class="abs" style="left:0;top:3460px" width="1200" height="514">
    <polygon points="20,98 600,10 1180,98 600,20" fill="#0f2447"/>
    <polygon points="0,115 600,26 1200,115 1200,514 0,514" fill="#0f2447"/>
  </svg>

  <section class="cta">
    <h2>Ready to Simplify Property Ownership?</h2>
    <p>Partner with a property management team that protects your investment while<br>delivering exceptional service every step of the way.</p>
    <a class="btn btn-white" style="left:309px;top:175px;width:196px;height:35px">Request Your Free Consultation</a>
    <span class="arrow-box btn-white" style="left:512px;top:175px;width:37px;height:35px"><svg viewBox="0 0 12 12"><path d="M3 9 9 3M4 3h5v5" fill="none" stroke="#17325e" stroke-width="1.4"/></svg></span>
  </section>

  <footer class="site-footer">
    <div class="footer-brand"><span class="brand-square"></span>Larkfield Ridge<br>Management</div>
    <div class="fcol" style="left:475px">
      <h4>Quick Link</h4>
      <ul><li>Home</li><li>Services</li><li>About</li><li>Properties</li><li>Resources</li><li>Contact</li></ul>
    </div>
    <div class="fcol" style="left:637px">
      <h4>Our Services</h4>
      <ul><li>Property Management</li><li>Tenant Placement</li><li>Maintenance</li><li>Financial Reporting</li><li>Inspections</li></ul>
    </div>
    <div class="fcol" style="left:831px">
      <h4>Contact Us</h4>
      <div class="contact-row"><svg viewBox="0 0 12 12"><path d="M2.5 1h2l1 3-1.5 1c.8 1.6 1.6 2.4 3 3l1-1.5 3 1v2c0 .8-.6 1.5-1.5 1.5C4.5 11 1 7.5 1 2.5 1 1.6 1.7 1 2.5 1Z" fill="#e8262b"/></svg><b>Call Us:</b>(440) 555-0142</div>
      <div class="contact-row"><svg viewBox="0 0 12 12"><rect x="1" y="2.5" width="10" height="7" fill="#e8262b"/><path d="M1 2.5 6 6.5l5-4" fill="none" stroke="#0f2447" stroke-width="1"/></svg><b>Email Address:</b>info@larkfieldridgemanagement.com</div>
      <div class="contact-row"><svg viewBox="0 0 12 12"><path d="M6 11S2 7 2 4.5a4 4 0 0 1 8 0C10 7 6 11 6 11Z" fill="#e8262b"/><circle cx="6" cy="4.5" r="1.4" fill="#0f2447"/></svg><b>Office Address:</b>410 Alder Avenue, Suite 300<br>Fairview, OH 44126</div>
    </div>
    <div class="footer-rule"></div>
    <p class="copyright">© Copyright 2026 Larkfield Ridge Management. All Rights Reserved.</p>
    <a class="to-top" aria-label="Back to top"><svg width="14" height="14" viewBox="0 0 14 14" fill="none" stroke="#fff" stroke-width="1.6"><path d="M7 12V2M3 6l4-4 4 4"/></svg></a>
  </footer>

</div>
</body>
</html>
```